Corvane Business Cards

Front of business card will have logo, name, address, & telephone number. Back of card will have a list of services provided - Roads, Substation Pads, Temporary Pads, Site Pads, Land Leveling, Powerline Row Cleaning, Land Clearing, Gates, Fencing, Construction Entrances, Excavation, Trenching, Underground Utilities, Directional Boring, Pile Driving. We are a construction company that uses heavy equipment like bulldozers, motor graders/blades, dump trucks, backhoes, hydro axes, & skid loaders. We build roads, pads, & install electric utility lines & waterlines underground. This logo is new. The word "Construction" can be smaller as uploaded 2 example edited logos. We will be using this card design for many employees.
Target Market(s)
Industrial Electric Powerline, Wind Turbine, Solar Panel, & Water Utility companies.
Contact Information for Business Card
Name/Position - Dwayne Halster - Owner
Address: 4875 FM 309
Brannock, TX 79412
Phone number - (325) 482-5096

```html
<!DOCTYPE html>
<html lang="en">
<head>
<meta charset="utf-8">
<title>Corvane Construction – Business Card</title>
<link href="https://fonts.googleapis.com/css2?family=Cinzel:wght@400;700&family=Arimo:wght@400;700&display=swap" rel="stylesheet">
<style>
  :root {
    --backdrop: #2e2e2e;
    --maroon: #3b0f18;
    --card-white: #ffffff;
    --ink: #2a2a2a;
    --ink-soft: #555555;
    --rule: rgba(255,255,255,0.35);
  }
  * { box-sizing: border-box; margin: 0; padding: 0; }
  html, body {
    width: 1200px; height: 866px; overflow: hidden;
    background: var(--backdrop);
  }
  .sheet {
    width: 1200px; height: 866px;
    display: flex; flex-direction: column;
    align-items: center; justify-content: center; gap: 40px;
  }
  .card {
    position: relative;
    width: 680px; height: 388px;
    overflow: hidden;
    box-shadow: 0 10px 24px rgba(0,0,0,0.45);
  }

  /* Front */
  .card-front { background: var(--card-white); }
  .brand-watermark {
    position: absolute; left: 0; top: 0;
    width: 470px; height: 190px;
    background: linear-gradient(180deg, #d4d4d4 0%, #f2f2f2 70%, rgba(255,255,255,0) 100%);
    clip-path: polygon(0 30%, 55% 30%, 70% 0, 100% 70%, 100% 100%, 0 100%);
    opacity: 0.8;
  }
  .contact {
    position: absolute; left: 48px; top: 150px;
    width: 300px;
  }
  .contact-name {
    font-family: "Cinzel", serif; font-weight: 700;
    font-size: 26px; line-height: 1.1; color: var(--maroon); letter-spacing: 0.5px;
    white-space: nowrap;
  }
  .contact-role {
    font-family: "Arimo", sans-serif; font-size: 20px;
    color: var(--ink-soft); margin-top: 4px;
  }
  .contact-phone {
    font-family: "Arimo", sans-serif; font-weight: 700;
    font-size: 24px; color: var(--ink); margin-top: 34px; letter-spacing: 0.5px;
    white-space: nowrap;
  }
  .contact-phone .label { color: var(--maroon); }
  .brand {
    position: absolute; right: 44px; top: 165px;
    display: flex; align-items: center; gap: 14px;
  }
  .brand-square { width: 26px; height: 26px; background: var(--maroon); flex: none; }
  .brand-name {
    font-family: "Cinzel", serif; font-weight: 700;
    font-size: 46px; line-height: 1; color: var(--maroon);
  }
  .brand-sub {
    font-family: "Cinzel", serif; font-weight: 700;
    font-size: 18px; letter-spacing: 3px; color: var(--maroon); margin-top: 6px;
  }
  .address {
    position: absolute; right: 44px; bottom: 34px;
    font-family: "Arimo", sans-serif; font-size: 21px; font-style: normal;
    color: var(--ink); text-align: right; line-height: 1.3;
  }

  /* Back */
  .card-back {
    background: var(--maroon);
    color: #fff;
    font-family: "Arimo", sans-serif;
    display: flex; flex-direction: column; align-items: center; justify-content: center;
    text-align: center; padding: 0 40px;
  }
  .services, .about { font-size: 17px; line-height: 1.45; }
  .divider { width: 300px; height: 1px; background: var(--rule); margin: 14px 0; }
</style>
</head>
<body>
<main class="sheet">
  <section class="card card-front" aria-label="Card front">
    <div class="brand-watermark" role="img" aria-label="Faint oversized brand decoration"></div>
    <div class="contact">
      <h1 class="contact-name">DWAYNE HALSTER</h1>
      <p class="contact-role">Owner</p>
      <p class="contact-phone"><span class="label">P:</span> (325) 482-5096</p>
    </div>
    <div class="brand">
      <span class="brand-square" aria-hidden="true"></span>
      <div class="brand-text">
        <p class="brand-name">CORVANE</p>
        <p class="brand-sub">CONSTRUCTION</p>
      </div>
    </div>
    <address class="address">4875 FM 309<br>Brannock, TX 79412</address>
  </section>

  <section class="card card-back" aria-label="Card back">
    <p class="services">
      Roads, Substation Pads | Temporary Pads | Site Pads,<br>
      Land Leveling | Powerline Row Cleaning | Land Clearing<br>
      Gates | Fencing,Construction Entrances | Excavation<br>
      Trenching | Underground Utilities | Directional Boring | Pile Driving.
    </p>
    <span class="divider"></span>
    <p class="about">
      We are a construction company that uses heavy equipment<br>
      like bulldozers | motor graders/blades | dump trucks<br>
      backhoes | hydro axes &amp; skid loaders.
    </p>
    <span class="divider"></span>
    <p class="about">
      We build roads, pads<br>
      install electric utility lines &amp; waterlines underground.
    </p>
  </section>
</main>
</body>
</html>
```